High end Electrical/home automation Business Card

Need a card for a high end electrical and home automation company utilising the existing logo.
Phone
Email
Website

Like black look with raised detail. Don’t necessarily need to keep colour of logo it could be made grayscale or white etc

Target Market(s)

High end clients

Contact Information for Business Card

Brightmoor Electrical

Requirements
Must have
• Logo, phone, email, website, address

High end look
Nice to have
• Black background card
Raised font
Should not have
• Lots of colour

```html
<!DOCTYPE html>
<html lang="en">
<head>
<meta charset="utf-8">
<title>Brightmoor Electrical — Business Card</title>
<link rel="stylesheet" href="https://fonts.googleapis.com/css2?family=Lato:wght@400;700&display=swap">
<style>
  :root {
    --backdrop: #2e2e2e;
    --card: #2a2a2a;
    --ink: #f2f2f2;
    --ink-soft: #dcdcdc;
    --foil: #a8a8a8;
    --rule: #8c8c8c;
  }
  * { margin: 0; padding: 0; box-sizing: border-box; }
  html, body { width: 1133px; height: 1200px; overflow: hidden; }
  body {
    background: var(--backdrop);
    font-family: "Lato", sans-serif;
    color: var(--ink);
    position: relative;
  }
  .card {
    position: absolute;
    left: 240px;
    width: 660px;
    height: 362px;
    background: var(--card);
  }
  .card--front { top: 192px; }
  .card--back { top: 624px; }

  .brand {
    display: flex;
    align-items: center;
    gap: 12px;
    font-weight: 700;
    white-space: nowrap;
  }
  .brand__dot {
    border-radius: 50%;
    flex: none;
  }
  .card--front .brand {
    position: absolute;
    left: 0; right: 0; top: 160px;
    justify-content: center;
    font-size: 32px;
    color: var(--foil);
  }
  .card--front .brand__dot { width: 26px; height: 26px; background: var(--foil); }

  .card--back .brand {
    position: absolute;
    right: 42px; top: 138px;
    font-size: 26px;
    color: var(--ink);
  }
  .card--back .brand__dot { width: 20px; height: 20px; background: var(--ink); }

  .person {
    position: absolute;
    left: 36px; top: 217px;
  }
  .person__name {
    font-size: 21px;
    font-weight: 400;
    letter-spacing: 0.5px;
    line-height: 1.1;
  }
  .person__title {
    font-size: 14px;
    color: var(--ink-soft);
    line-height: 1.3;
  }
  .rule {
    position: absolute;
    left: 36px; right: 44px; top: 267px;
    height: 1px;
    background: var(--rule);
  }
  .contacts {
    position: absolute;
    left: 36px; top: 279px;
    list-style: none;
    font-size: 15px;
    line-height: 19px;
  }
  .contacts li { display: flex; align-items: center; gap: 9px; }
  .contacts svg { width: 12px; height: 12px; fill: var(--ink); flex: none; }
  .address {
    position: absolute;
    right: 42px; top: 279px;
    font-style: normal;
    text-align: right;
    font-size: 15px;
    line-height: 19px;
  }
</style>
</head>
<body>
  <section class="card card--front">
    <div class="brand"><span class="brand__dot"></span>Brightmoor Electrical</div>
  </section>

  <section class="card card--back">
    <div class="brand"><span class="brand__dot"></span>Brightmoor Electrical</div>

    <div class="person">
      <h1 class="person__name">DANIEL HARWOOD</h1>
      <p class="person__title">President</p>
    </div>

    <div class="rule"></div>

    <ul class="contacts">
      <li>
        <svg viewBox="0 0 24 24" aria-hidden="true"><path d="M6.6 10.8a15.1 15.1 0 0 0 6.6 6.6l2.2-2.2c.3-.3.7-.4 1-.2 1.1.4 2.3.6 3.6.6.6 0 1 .4 1 1V20c0 .6-.4 1-1 1C10.6 21 3 13.4 3 4c0-.6.4-1 1-1h3.5c.6 0 1 .4 1 1 0 1.3.2 2.5.6 3.6.1.3 0 .7-.2 1z"/></svg>
        555-014-2738
      </li>
      <li>
        <svg viewBox="0 0 24 24" aria-hidden="true"><path d="M2 5h20v14H2z M2 5l10 8 10-8" /><path d="M3 6.5l9 7 9-7V18H3z" fill="var(--card)"/></svg>
        info@brightmoorelectrical.com
      </li>
      <li>
        <svg viewBox="0 0 24 24" aria-hidden="true"><circle cx="12" cy="12" r="10"/><path d="M7 8c2 0 3 1 3 3s-2 2-2 4 1 3 1 4c-2-1-5-3-5-7 0-2 1-4 3-4zm9-2c1 1 2 2 1 3s-2 1-2 3 2 2 2 4c2-1 3-3 3-5s-2-4-4-5z" fill="var(--card)"/></svg>
        www.brightmoorelectrical.com
      </li>
    </ul>

    <address class="address">
      Brightmoor Electrical LLC<br>
      4120 Juniper Court<br>
      Fairview, Oregon 97024
    </address>
  </section>
</body>
</html>
```